Web Design For Manufacturing And Outsourcing Company

Pick up the pieces from our previous developer and help us complete our website.

5 pages - Home,Machining,Sourcing,About Us, and Contact

Attached you will find screen shots of previous direction but we're open to new ideas.

We can provide all text and images needed.

Thanks!

Number of Pages Required

5+ page

```html
<!DOCTYPE html>
<html lang="en">
<head>
<meta charset="utf-8">
<title>Calder Industries — Machining &amp; Sourcing</title>
<link rel="stylesheet" href="https://fonts.googleapis.com/css2?family=Roboto:wght@400;500;700&family=Open+Sans:wght@400;600&display=swap">
<style>
:root{
  --orange:#e8531f;
  --orange-dark:#c9420f;
  --ink:#222222;
  --text:#3a3a3a;
  --muted:#5a5a5a;
  --charcoal:#3b3b3e;
  --white:#ffffff;
  --paper:#f2f2f2;
}
*{box-sizing:border-box;margin:0;padding:0}
html,body{width:1200px;height:3435px;overflow:hidden}
body{position:relative;background:var(--white);font-family:"Open Sans",Arial,sans-serif;color:var(--text)}
.abs{position:absolute}
.heading{font-family:"Roboto",Arial,sans-serif;font-weight:700;color:var(--ink);text-transform:uppercase}

/* hero */
.hero{position:absolute;left:0;top:0;width:1200px;height:620px;overflow:hidden}
.hero-photo{position:absolute;left:0;top:0;width:1200px;height:620px;background:linear-gradient(120deg,#d9d9d9 0%,#eeeeee 45%,#b9b9b9 70%,#efefef 100%)}
.hero svg{position:absolute;left:0;top:0}
.brand{font-family:"Roboto",Arial,sans-serif;font-weight:700;letter-spacing:3px;text-transform:uppercase;display:flex;align-items:center;gap:12px}
.brand-square{width:26px;height:26px;background:var(--white)}
.hero .brand{position:absolute;left:155px;top:52px;color:var(--white);font-size:16px}
.nav{display:flex;gap:30px;font-family:"Roboto",Arial,sans-serif;font-weight:700;font-size:15px;text-transform:uppercase}
.hero .nav{position:absolute;left:512px;top:63px;color:var(--ink)}
.hero .nav a:first-child{color:var(--white)}
.nav a{color:inherit;text-decoration:none}
.hero-title{position:absolute;left:172px;top:220px;width:520px;font-family:"Roboto",Arial,sans-serif;font-weight:700;font-size:34px;line-height:46px;color:var(--white);text-transform:uppercase}
.btn{display:flex;align-items:center;justify-content:center;background:var(--orange);color:var(--white);font-family:"Roboto",Arial,sans-serif;font-weight:700;font-size:16px;text-transform:uppercase;text-decoration:none}
.hero .btn{position:absolute;left:172px;top:372px;width:164px;height:40px}
.slide-arrow{position:absolute;top:288px;width:52px;height:52px;border-radius:50%;background:rgba(80,80,80,.7)}
.slide-arrow.prev{left:80px}
.slide-arrow.next{left:1027px}

/* about */
.about-mark{left:540px;top:535px;width:120px;text-align:center;font-family:"Roboto",Arial,sans-serif;font-weight:700;font-size:14px;letter-spacing:2px;color:var(--ink);text-transform:uppercase}
.about-title{left:0;top:605px;width:1200px;text-align:center;font-size:36px}
.policy-title{left:0;top:684px;width:1200px;text-align:center;font-family:"Roboto",Arial,sans-serif;font-weight:700;font-size:22px;color:var(--orange);text-transform:uppercase}
.policy-text{left:262px;top:724px;width:680px;text-align:center;font-size:16px;line-height:28px;color:var(--ink)}
.values-title{left:0;top:890px;width:1200px;text-align:center;font-size:23px;color:var(--ink)}
.value{position:absolute;top:955px;width:260px;display:flex;gap:12px}
.value svg{flex:none}
.value h3{font-family:"Roboto",Arial,sans-serif;font-weight:700;font-size:16px;color:var(--orange);text-transform:uppercase;margin-bottom:6px}
.value p{font-size:13.5px;line-height:19px;color:var(--muted)}
.value .more{display:block;margin-top:10px;font-family:"Roboto",Arial,sans-serif;font-weight:700;font-size:13px;color:var(--text);text-transform:uppercase}
.about-bg{left:0;top:560px;width:1200px;height:660px;background:linear-gradient(180deg,#ffffff 0%,#ececec 100%)}

/* sourcing */
.sourcing-bg{position:absolute;left:0;top:1170px}
.sourcing-title{left:0;top:1235px;width:1200px;text-align:center;font-size:34px;color:var(--white)}
.sourcing-sub{left:0;top:1287px;width:1200px;text-align:center;font-family:"Roboto",Arial,sans-serif;font-size:19px;color:var(--white)}
.intro{font-size:13px;line-height:21px}
.sourcing-intro{left:167px;top:1368px;width:430px;color:var(--white)}
.feature{position:absolute;display:flex;gap:18px;align-items:flex-start}
.feature h3{font-family:"Roboto",Arial,sans-serif;font-weight:700;font-size:19px;margin-bottom:2px}
.feature p{font-size:13.5px;line-height:20px}
.sourcing-feature{left:170px;width:430px;color:var(--white)}
.sourcing-frame{left:623px;top:1395px;width:413px;height:478px;border:2px solid rgba(255,255,255,.8)}
.sourcing-photo{left:641px;top:1365px;width:410px;height:490px;background:linear-gradient(160deg,#35656e 0%,#5b9aa1 45%,#1f3d47 100%)}

/* machining */
.machining-title{left:0;top:2048px;width:1200px;text-align:center;font-size:32px}
.machining-sub{left:0;top:2098px;width:1200px;text-align:center;font-family:"Roboto",Arial,sans-serif;font-size:22px;color:var(--ink)}
.machining-frame{left:142px;top:2190px;width:412px;height:496px;border:2px solid var(--orange)}
.machining-photo{left:158px;top:2178px;width:410px;height:492px;background:linear-gradient(150deg,#9fb6c9 0%,#5d7b94 40%,#2a3c4f 75%,#7d95aa 100%)}
.machining-intro{left:606px;top:2164px;width:480px;color:var(--text)}
.machining-feature{left:610px;width:480px;color:var(--text)}
.machining-feature h3{font-weight:400;font-size:21px;color:var(--ink)}

/* call to action */
.cta-bg{position:absolute;left:0;top:2770px}
.cta-mark{left:0;top:2905px;width:1200px;text-align:center;font-family:"Roboto",Arial,sans-serif;font-weight:700;font-size:15px;letter-spacing:3px;color:var(--white);text-transform:uppercase}
.cta-title{left:0;top:2966px;width:1200px;text-align:center;font-family:"Roboto",Arial,sans-serif;font-size:32px;line-height:44px;color:var(--white);text-transform:uppercase}
.cta-btn{left:497px;top:3072px;width:202px;height:50px;font-size:17px}

/* footer */
.footer .brand{position:absolute;left:126px;top:3304px;color:var(--ink);font-size:15px}
.footer .brand-square{background:var(--orange)}
.footer .brand span{color:var(--orange)}
.footer .nav{position:absolute;left:390px;top:3313px;gap:18px;font-size:14.5px;color:var(--ink)}
.copyright{left:390px;top:3343px;font-family:"Roboto",Arial,sans-serif;font-weight:500;font-size:12.5px;color:var(--muted)}
.social{position:absolute;left:915px;top:3308px;display:flex;gap:10px}
.social span{width:28px;height:28px;border-radius:50%;background:#2f4f8a}
</style>
</head>
<body>

<header class="hero">
  <div class="hero-photo" role="img" aria-label="Close-up photograph of a CNC lathe machining a steel shaft"></div>
  <svg width="1200" height="620" viewBox="0 0 1200 620" aria-hidden="true">
    <defs>
      <linearGradient id="heroOrange" x1="0" y1="0" x2="1" y2="1">
        <stop offset="0" stop-color="#b54a24" stop-opacity=".95"/>
        <stop offset="1" stop-color="#e8531f" stop-opacity=".95"/>
      </linearGradient>
    </defs>
    <path d="M0 0 H795 C770 260 590 612 250 612 C150 612 60 590 0 560 Z" fill="url(#heroOrange)"/>
  </svg>
  <div class="brand"><span class="brand-square"></span>Calder Industries</div>
  <nav class="nav"><a href="#">Home</a><a href="#">Machining Capabilities</a><a href="#">Sourcing</a><a href="#">Contact Us</a></nav>
  <h1 class="hero-title">A single point of contact for all your procurement needs</h1>
  <a class="btn" href="#">Read More</a>
  <span class="slide-arrow prev"><svg width="52" height="52" viewBox="0 0 52 52"><path d="M30 17 L21 26 L30 35" stroke="#fff" stroke-width="3" fill="none"/></svg></span>
  <span class="slide-arrow next"><svg width="52" height="52" viewBox="0 0 52 52"><path d="M22 17 L31 26 L22 35" stroke="#fff" stroke-width="3" fill="none"/></svg></span>
</header>

<section class="about">
  <div class="abs about-bg"></div>
  <div class="abs about-mark">Calder</div>
  <h2 class="abs heading about-title">About Us</h2>
  <h3 class="abs policy-title">Quality Policy</h3>
  <p class="abs policy-text">We are committed to consistently exceeding customer expectations by providing products, services and sourcing solutions of the highest standard of quality. With our streamlined processes our method is efficient, provides value and ensures on time delivery. Our success isbased on continuously improving the efficiencies and effectiveness of our products</p>
  <h2 class="abs heading values-title">Core Values</h2>

  <div class="value" style="left:192px">
    <svg width="56" height="56" viewBox="0 0 56 56" fill="none" stroke="#e8531f" stroke-width="2.5"><circle cx="16" cy="14" r="7"/><circle cx="40" cy="14" r="7"/><circle cx="28" cy="26" r="7"/><path d="M6 40 q10-14 20 0 M30 40 q10-14 20 0 M16 52 q12-16 24 0"/></svg>
    <div><h3>Teamwork</h3><p>We are one company, one team. We understand when we work together we work smarter and not harder.</p><span class="more">Read More</span></div>
  </div>
  <div class="value" style="left:462px">
    <svg width="62" height="56" viewBox="0 0 62 56" fill="none" stroke="#e8531f" stroke-width="2.5"><path d="M4 22 L16 10 L30 18 L44 10 L58 22 L40 42 Q34 48 28 42 Z"/><path d="M22 30 L32 40 M28 26 L38 36"/></svg>
    <div><h3>Respect</h3><p>We are one company, one team. We understand when we work together we work smarter and not harder.</p><span class="more">Read More</span></div>
  </div>
  <div class="value" style="left:785px">
    <svg width="56" height="56" viewBox="0 0 56 56" fill="none" stroke="#e8531f" stroke-width="2.5"><path d="M12 20 V8 h8 v12 M20 18 V6 h8 v12 M28 18 V8 h8 v12 M36 20 V12 h8 v14 Q44 40 32 44 V52 H18 V42 Q10 36 10 26 Z"/></svg>
    <div><h3>Gratitude</h3><p>We appreciate where we have come from and the opportunities we are given to continue our journey.</p><span class="more">Read More</span></div>
  </div>
</section>

<section class="sourcing">
  <svg class="sourcing-bg" width="1200" height="860" viewBox="0 0 1200 860" aria-hidden="true">
    <path d="M0 90 C300 30 800 10 1200 20 V120 H0 Z" fill="#3b3b3e"/>
    <path d="M0 110 C320 55 800 40 1200 58 V795 C900 835 400 830 0 800 Z" fill="#e8531f"/>
    <path d="M620 800 C900 790 1100 740 1200 700 V795 C1000 840 820 845 620 800 Z" fill="#3b3b3e"/>
  </svg>
  <h2 class="abs heading sourcing-title">Sourcing</h2>
  <p class="abs sourcing-sub">Minimizing Costs by Providing Specific Sourcing Solutions for Each Individual Job!</p>
  <p class="abs intro sourcing-intro">Pellentesque faucibus Ut accumsan ultricies elit Maecenas at justo id velit placerat molestie Donec dictum lectus non odio Cras a ante vitae enim iaculis aliquam Mauris nunc quam venenatis nec</p>

  <div class="feature sourcing-feature" style="top:1465px">
    <svg width="52" height="52" viewBox="0 0 52 52" fill="none" stroke="#fff" stroke-width="2"><circle cx="26" cy="26" r="20"/><circle cx="26" cy="26" r="8"/><path d="M26 2 v8 M26 42 v8 M2 26 h8 M42 26 h8"/></svg>
    <div><h3>Vetting</h3><p>Pellentesque faucibus Ut accumsan ultricies elit Maecenas at justo id velit placerat molestie</p></div>
  </div>
  <div class="feature sourcing-feature" style="top:1575px">
    <svg width="52" height="52" viewBox="0 0 52 52" fill="none" stroke="#fff" stroke-width="2"><circle cx="26" cy="26" r="21" stroke-dasharray="5 3"/><circle cx="26" cy="26" r="14"/><path d="M26 17 l3 6 6 1 -4.5 4 1 6 -5.5-3 -5.5 3 1-6 -4.5-4 6-1 Z"/></svg>
    <div><h3>Quality</h3><p>Pellentesque faucibus Ut accumsan ultricies elit Maecenas at justo id velit placerat molestie</p></div>
  </div>
  <div class="feature sourcing-feature" style="top:1685px">
    <svg width="52" height="52" viewBox="0 0 52 52" fill="none" stroke="#fff" stroke-width="2"><circle cx="26" cy="26" r="21"/><circle cx="26" cy="26" r="13"/><circle cx="26" cy="26" r="5"/></svg>
    <div><h3>Process</h3><p>Pellentesque faucibus Ut accumsan ultricies elit Maecenas at justo id velit placerat molestie</p></div>
  </div>
  <div class="feature sourcing-feature" style="top:1795px">
    <svg width="52" height="52" viewBox="0 0 52 52" fill="none" stroke="#fff" stroke-width="2"><rect x="6" y="8" width="40" height="28"/><path d="M12 30 L22 20 L30 26 L40 14 M26 36 v10 M18 48 h16"/></svg>
    <div><h3>Benefits</h3><p>Pellentesque faucibus Ut accumsan ultricies elit Maecenas at justo id velit placerat molestie</p></div>
  </div>

  <div class="abs sourcing-frame"></div>
  <div class="abs sourcing-photo" role="img" aria-label="Business partners shaking hands over a glowing digital network of connections"></div>
</section>

<section class="machining">
  <h2 class="abs heading machining-title">Machining</h2>
  <p class="abs machining-sub">Our In-house capablities</p>
  <div class="abs machining-frame"></div>
  <div class="abs machining-photo" role="img" aria-label="CNC turning machine cutting a metal part"></div>
  <p class="abs intro machining-intro">Pellentesque faucibus Ut accumsan ultricies elit Maecenas at justo id velit placerat molestie Donec dictum lectus non odio Cras a ante vitae enim iaculis aliquam Mauris nunc quam venenatis nec</p>

  <div class="feature machining-feature" style="top:2256px">
    <svg width="62" height="62" viewBox="0 0 62 62" fill="none" stroke="#e8531f" stroke-width="2"><rect x="8" y="44" width="24" height="10"/><path d="M20 44 V30 L36 16 L46 24"/><circle cx="20" cy="30" r="4"/><circle cx="44" cy="44" r="9"/><circle cx="44" cy="44" r="3"/></svg>
    <div><h3>Multiple Axis Equipment</h3><p>Pellentesque faucibus Ut accumsan ultricies elit Maecenas at justo id velit placerat molestie Donec dictum</p></div>
  </div>
  <div class="feature machining-feature" style="top:2364px">
    <svg width="62" height="62" viewBox="0 0 62 62" fill="none" stroke="#e8531f" stroke-width="2"><rect x="8" y="8" width="30" height="46"/><path d="M14 16 h18 M14 24 h18 M14 32 h12"/><rect x="30" y="30" width="24" height="24"/><path d="M36 42 h12"/></svg>
    <div><h3>Tolerances of =/.0001</h3><p>Pellentesque faucibus Ut accumsan ultricies elit Maecenas at justo id velit placerat molestie Donec dictum</p></div>
  </div>
  <div class="feature machining-feature" style="top:2472px">
    <svg width="62" height="62" viewBox="0 0 62 62" fill="none" stroke="#e8531f" stroke-width="2"><rect x="20" y="4" width="22" height="10"/><path d="M22 18 h18 M22 24 h18 M22 30 h18 M24 36 h14 M26 42 h10 M28 48 h6 M31 48 v10"/></svg>
    <div><h3>Custom Built Fixtures</h3><p>Pellentesque faucibus Ut accumsan ultricies elit Maecenas at justo id velit placerat molestie Donec dictum</p></div>
  </div>
  <div class="feature machining-feature" style="top:2576px">
    <svg width="62" height="62" viewBox="0 0 62 62" fill="none" stroke="#e8531f" stroke-width="2"><rect x="6" y="10" width="50" height="44"/><circle cx="31" cy="34" r="12"/><path d="M31 26 v8 l6 4 M6 18 h50"/></svg>
    <div><h3>Prototypes to Production Runs</h3><p>Pellentesque faucibus Ut accumsan ultricies elit Maecenas at justo id velit placerat molestie Donec dictum</p></div>
  </div>
</section>

<section class="cta">
  <svg class="cta-bg" width="1200" height="500" viewBox="0 0 1200 500" aria-hidden="true">
    <defs>
      <linearGradient id="ctaDark" x1="0" y1="0" x2="1" y2="1">
        <stop offset="0" stop-color="#2e2e31"/>
        <stop offset=".5" stop-color="#4a4a4e"/>
        <stop offset="1" stop-color="#2a2a2c"/>
      </linearGradient>
    </defs>
    <path d="M0 10 C400 10 900 40 1200 120 V430 C800 470 300 490 0 480 Z" fill="url(#ctaDark)"/>
    <path d="M700 18 C950 30 1110 70 1200 105 V125 C1080 80 900 45 700 18 Z" fill="#e8531f"/>
    <path d="M0 395 C200 450 420 475 620 480 C400 492 150 488 0 470 Z" fill="#e8531f"/>
    <rect x="0" y="0" width="1200" height="500" fill="none"/>
  </svg>
  <div class="abs cta-mark">Calder</div>
  <h2 class="abs cta-title">Contact us today with your machining<br>or sourcing needs!</h2>
  <a class="abs btn cta-btn" href="#">Get In Touch</a>
</section>

<footer class="footer">
  <div class="brand"><span class="brand-square"></span><span>Calder Industries</span></div>
  <nav class="nav"><a href="#">Home</a><a href="#">Machining Capabilities</a><a href="#">Sourcing</a><a href="#">Contact Us</a></nav>
  <p class="abs copyright">© 2019 Company Name  All right reserved</p>
  <div class="social" aria-label="Social media links"><span></span><span></span><span></span><span></span></div>
</footer>

</body>
</html>
```